Luxury Wine Label for New Startup Winery

We need a wine label for our new winery startup. We have worked with a local designer but do not feel the resulting label / logo have the elevation required to present our brand as a luxury wine. Our winery is called "Quailbrook Vineyards" and we are focused on extremely high quality hand crafted artisan and estate wines from the Pacific Northwest.
We would like to see designs that utilize a tree line, or other imagery that represents the "Quailbrook" part of our company name. Another interesting feature could be wood grain.
A logo will be required based on your design so please design with this in mind:
This logo should be consistent with the wine bottle label design, and should be representative of our high end exclusive wine while giving a sense of place (Oregon/ Pacific Northwest.)
I will supply an image of the design we received from our local designer, PLEASE NOTE: in general we do like wood grain and tree line concepts but feel the execution was poorly done.
ATTN: Logo design should be suitable for use on: Bottles (Red wine/rose/white wine), Bussiness cards, vehicle signage, business signage, etc
P.S.:
If you have a design that is not outside the box we are still interested in seeing it.
Label is for a burgundy style bottle with a label height of 3.5 - 4" and a width of 3.5-4"
any label <= 4"x4" and >=3.5"x3.5" will be acceptable:
HOWEVER Width should be greater than or equal to height due to the bottle format
Target Market(s)
Wine enthusiasts with adequate discretionary budgets to afford $100 bottles of wine.
Industry/Entity Type
Wine / Winery
Requirements
Must have
- A sense of luxury, a feel of exclusivity, and a theme consistent with our product and brand name
Nice to have
- Tree line, wood grain or other wood themes. Serif fonts
Should not have
- anything cheesy, off topic, hard to read script fonts or anything that makes the label hard to read from a few feet away or too busy

```html
<!DOCTYPE html>
<html lang="en">
<head>
<meta charset="utf-8">
<title>Quailbrook Vineyards — Syrah Label</title>
<link rel="stylesheet" href="https://fonts.googleapis.com/css2?family=Josefin+Sans:wght@400;600&display=swap">
<style>
  :root {
    --backdrop: #e4e4e4;
    --label-black: #141414;
    --wood-dark: #2a1d12;
    --wood-mid: #5a3f26;
    --wood-light: #7a5a3a;
    --ink-white: #f2efe9;
    --gold: #c9963f;
    --gold-light: #e0b35d;
    --wax-gold: #d89a2e;
    --wax-red: #b3223a;
  }
  * { box-sizing: border-box; margin: 0; padding: 0; }
  html, body { width: 1200px; height: 900px; overflow: hidden; }
  body {
    background: var(--backdrop);
    font-family: "Josefin Sans", sans-serif;
    display: flex;
    justify-content: center;
    align-items: center;
    gap: 90px;
  }
  .label {
    position: relative;
    width: 430px;
    height: 410px;
    border-radius: 16px;
    background: var(--label-black);
  }
  .label__artwork {
    position: absolute;
    inset: 0 0 auto 0;
    height: 280px;
    border-radius: 16px 16px 0 0;
    background:
      linear-gradient(180deg, rgba(20,20,20,0) 0%, rgba(20,20,20,0) 55%, rgba(20,20,20,0.75) 82%, var(--label-black) 100%),
      linear-gradient(90deg, var(--wood-dark) 0%, var(--wood-mid) 22%, var(--wood-light) 50%, var(--wood-mid) 78%, var(--wood-dark) 100%);
  }
  .label__seal {
    position: absolute;
    top: -22px;
    left: 50%;
    width: 106px;
    height: 106px;
    margin-left: -53px;
    border-radius: 50%;
  }
  .label--gold .label__seal { background: var(--wax-gold); }
  .label--red .label__seal { background: var(--wax-red); }
  .label__text {
    position: absolute;
    left: 0; right: 0;
    text-align: center;
    line-height: 1;
  }
  .label__brand {
    top: 116px;
    color: var(--ink-white);
    font-weight: 600;
    font-size: 40px;
    letter-spacing: 0.06em;
  }
  .label__sub {
    top: 166px;
    color: var(--ink-white);
    font-weight: 400;
    font-size: 19px;
    letter-spacing: 0.32em;
  }
  .label__varietal {
    top: 292px;
    color: var(--gold);
    font-weight: 600;
    font-size: 40px;
    letter-spacing: 0.2em;
  }
  .label__region {
    top: 350px;
    color: var(--gold-light);
    font-weight: 400;
    font-size: 15px;
    letter-spacing: 0.12em;
    line-height: 1.45;
  }
</style>
</head>
<body>
  <article class="label label--gold">
    <div class="label__artwork" role="img" aria-label="Vertical wood grain panel fading into a dark evergreen tree line silhouette"></div>
    <div class="label__seal" aria-hidden="true"></div>
    <h1 class="label__text label__brand">QUAILBROOK</h1>
    <p class="label__text label__sub">VINEYARDS</p>
    <h2 class="label__text label__varietal">SYRAH</h2>
    <p class="label__text label__region">WILLAMETTE VALLEY<br>2024</p>
  </article>

  <article class="label label--red">
    <div class="label__artwork" role="img" aria-label="Vertical wood grain panel fading into a dark evergreen tree line silhouette"></div>
    <div class="label__seal" aria-hidden="true"></div>
    <h1 class="label__text label__brand">QUAILBROOK</h1>
    <p class="label__text label__sub">VINEYARDS</p>
    <h2 class="label__text label__varietal">SYRAH</h2>
    <p class="label__text label__region">WILLAMETTE VALLEY<br>2024</p>
  </article>
</body>
</html>
```